Business Card Design Project

Double-side business card.
Side One:
Logo (Including the word VELUNTA that is part of the Logo
"Programas de Cooperación Comunitaria y Renovación del Entorno Natural Local"
Side Two:
Marisol Ontiveros
Co-Founder & CEO
Washington, DC (USA)
email: marisolo@velunta.net (please use an icon for "emal")
cell: +1 (202) 555 0147 (please use an icon for "cell")
skype: marisolontiv (please use an icon for "skype")
twitter: marisolontiv (please use an icon for "twitter")
www.velunta.net
Target Market(s)
Foundations, Governments, and Private sector companies that implement projects for sustainability.
Industry/Entity Type
Business
Colors
Designer to choose colors to be used in the design.
Requirements
Nice to have
- barcode

```html
<!DOCTYPE html>
<html lang="es">
<head>
<meta charset="utf-8">
<title>VELUNTA – Business Card</title>
<link rel="stylesheet" href="https://fonts.googleapis.com/css2?family=Fira+Sans+Condensed:wght@400;600;700&display=swap">
<style>
  :root {
    --backdrop: #e9e6e1;
    --card: #f7f7f5;
    --ink-grey: #6f7479;
    --ink-soft: #8d9297;
    --teal: #1f6f78;
    --band: #c9cbcc;
    --shadow: rgba(40, 30, 20, 0.18);
  }
  * { box-sizing: border-box; margin: 0; padding: 0; }
  html, body {
    width: 1200px; height: 845px; overflow: hidden;
    background: var(--backdrop);
    font-family: "Fira Sans Condensed", "Arial Narrow", sans-serif;
  }
  .sheet {
    width: 1200px; height: 845px;
    display: flex; align-items: center; justify-content: center; gap: 40px;
  }
  .card {
    position: relative;
    width: 540px; height: 309px;
    background: var(--card);
    box-shadow: 0 6px 18px var(--shadow);
    overflow: hidden;
  }

  /* Front side */
  .card--front {
    display: flex; flex-direction: column; align-items: center; justify-content: center;
    text-align: center;
  }
  .brand-mark {
    display: flex; align-items: center; gap: 16px;
  }
  .brand-mark__dot {
    width: 34px; height: 34px; border-radius: 50%; background: var(--teal);
  }
  .brand-mark__name {
    font-size: 64px; font-weight: 400; letter-spacing: 8px; color: var(--ink-soft);
    line-height: 1;
  }
  .tagline {
    margin-top: 16px; max-width: 440px;
    font-size: 14px; font-weight: 600; color: var(--teal);
  }

  /* Back side */
  .band {
    position: absolute; left: 0; right: 0; top: 138px; height: 34px;
    background: var(--band);
  }
  .band__line {
    position: absolute; left: 0; right: 0; top: 22px; height: 3px;
    background: var(--teal);
  }
  .badge {
    position: absolute; left: 50%; top: 155px;
    width: 96px; height: 96px; margin: -48px 0 0 -48px;
    border-radius: 50%; background: var(--teal);
    border: 4px solid var(--card);
    display: flex; align-items: center; justify-content: center;
  }
  .badge__name {
    font-size: 17px; font-weight: 400; letter-spacing: 2px; color: #ffffff;
  }
  .identity {
    position: absolute; left: 34px; top: 40px;
  }
  .identity__name {
    font-size: 32px; font-weight: 700; color: var(--ink-grey); line-height: 1.05;
  }
  .identity__name span { color: var(--teal); }
  .identity__role {
    margin-top: 4px; font-size: 16px; font-weight: 600; color: var(--ink-grey);
  }
  .contact-list {
    position: absolute; list-style: none;
    font-size: 13px; color: var(--ink-grey);
  }
  .contact-list li {
    display: flex; align-items: center; gap: 9px; height: 22px;
  }
  .contact-list svg { width: 14px; height: 14px; flex: none; }
  .contact-list--top { right: 34px; top: 38px; }
  .contact-list--bottom { left: 34px; bottom: 30px; }
  .icon-dot {
    width: 13px; height: 13px; border-radius: 50%; background: var(--teal); flex: none;
  }
</style>
</head>
<body>
<main class="sheet">

  <section class="card card--front" aria-label="Front side">
    <div class="brand-mark">
      <span class="brand-mark__dot"></span>
      <span class="brand-mark__name">VELUNTA</span>
    </div>
    <p class="tagline">“Programas de Cooperación Comunitaria y Renovación del Entorno Natural Local”</p>
  </section>

  <section class="card card--back" aria-label="Back side">
    <div class="band"><div class="band__line"></div></div>
    <div class="badge"><span class="badge__name">VELUNTA</span></div>

    <div class="identity">
      <h1 class="identity__name">Marisol <span>Ontiveros</span></h1>
      <p class="identity__role">Co-Founder &amp; CEO</p>
    </div>

    <ul class="contact-list contact-list--top">
      <li>
        <svg viewBox="0 0 14 14" aria-hidden="true"><rect x="3" y="1" width="8" height="12" rx="1.5" fill="none" stroke="#1f6f78" stroke-width="1.4"/><circle cx="7" cy="10.8" r="0.9" fill="#1f6f78"/></svg>
        +1 (202) 555 0147
      </li>
      <li>
        <svg viewBox="0 0 14 14" aria-hidden="true"><rect x="1" y="3" width="12" height="8" rx="1" fill="none" stroke="#1f6f78" stroke-width="1.4"/><path d="M1.5 3.5 L7 8 L12.5 3.5" fill="none" stroke="#1f6f78" stroke-width="1.4"/></svg>
        marisolo@velunta.net
      </li>
      <li>
        <svg viewBox="0 0 14 14" aria-hidden="true"><circle cx="7" cy="7" r="6" fill="none" stroke="#1f6f78" stroke-width="1.3"/><ellipse cx="7" cy="7" rx="2.6" ry="6" fill="none" stroke="#1f6f78" stroke-width="1.1"/><path d="M1 7 H13" stroke="#1f6f78" stroke-width="1.1"/></svg>
        www.velunta.net
      </li>
    </ul>

    <ul class="contact-list contact-list--bottom">
      <li>
        <svg viewBox="0 0 14 14" aria-hidden="true"><path d="M1 7 L7 1.5 L13 7 H11 V13 H3 V7 Z" fill="#1f6f78"/></svg>
        Washington, DC (USA)
      </li>
      <li><span class="icon-dot"></span>marisolontiv</li>
      <li><span class="icon-dot"></span>marisolontiv</li>
    </ul>
  </section>

</main>
</body>
</html>
```